Refresh of far from plain IT company website

Our web site is starting to show it's age. You can see the existing site here: www.plumbwick.net. As a growing company we want to come across as a dynamic collection of IT experts.

We want to update the design so are open to any colour palette and look, but want to retain our current table logo. We use the logo on our business cards but with a white background - see the attached file, so you don't need to keep the brown or the green.

The design should consider the range of browsers that will be looking at the site - so please show how it will look on a wide screen laptop and a 768x1024 tablet.

We want to add some pages about our team and their skills, probably with photos of each person on the team.

This is an uncoded project - the PSD files of the design is required, not coding.
Updates

Thanks everyone for the submissions so far.  It's a holiday day in the UK today but we will get some feedback on the designs so far out to you.

Target Market(s)

Architects and other creative types looking for IT support

Industry/Entity Type

Business

Font styles to use
Serif
Sans Serif

Requirements
Must have
• Must look good on a laptop and an iPad.

```html
<!DOCTYPE html>
<html lang="en">
<head>
<meta charset="utf-8">
<title>plumbwick – Serious IT support for business</title>
<link href="https://fonts.googleapis.com/css2?family=Ubuntu:ital,wght@0,400;0,500;0,700;1,700&family=Roboto:wght@400;500&display=swap" rel="stylesheet">
<style>
:root{
  --plum:#8e0d4f;
  --plum-dark:#6f0a3d;
  --gold:#d8a90a;
  --ink:#333;
  --muted:#666;
  --line:#e2e2e2;
  --panel:#efefef;
  --footer:#333;
  --icon:#555;
}
*{box-sizing:border-box;margin:0;padding:0}
html,body{width:1034px;height:1200px;overflow:hidden;background:#fff}
body{position:relative;font-family:"Roboto",Arial,sans-serif;color:var(--ink)}
.abs{position:absolute}
.topbar{left:0;top:0;width:1034px;height:3px;background:var(--plum)}
.brand{left:197px;top:26px;display:flex;align-items:center;gap:12px}
.brand-mark{width:30px;height:30px;background:var(--gold)}
.brand-name{font-family:"Ubuntu",sans-serif;font-weight:500;font-size:44px;color:var(--plum);line-height:1;letter-spacing:-.5px}
.callus{right:192px;top:18px;font-family:"Ubuntu",sans-serif;font-size:14px;color:#444;letter-spacing:.3px}
.social{right:192px;top:54px;display:flex;gap:6px}
.social span{width:27px;height:27px;border-radius:50%;background:#e6e6e6;box-shadow:0 2px 3px rgba(0,0,0,.2)}
.social span:first-child{background:#1b8fc9}
.nav{left:192px;top:97px;width:654px;display:flex;justify-content:space-between;font-family:"Ubuntu",sans-serif;font-size:9.5px;text-transform:uppercase;letter-spacing:.3px}
.nav a{color:#555;text-decoration:none;padding:0 8px;height:25px;line-height:14px;position:relative}
.nav a+a::before{content:"";position:absolute;left:-4px;top:2px;height:11px;border-left:1px solid #ccc}
.nav a.active{color:var(--plum);font-weight:700}
.nav a.active::after{content:"";position:absolute;left:4px;right:0;bottom:0;height:3px;background:var(--plum)}
.hero{left:0;top:122px;width:1034px;height:332px;background:linear-gradient(135deg,#cfe0f2 0%,#6fa6e0 35%,#2b6fd0 70%,#1450b8 100%)}
.hero-photo{left:0;top:122px;width:560px;height:332px;background:radial-gradient(ellipse at 35% 60%,rgba(196,150,120,.55),rgba(196,150,120,0) 70%)}
.hero-title{left:555px;top:358px;font-family:"Ubuntu",sans-serif;font-size:21px;color:#fff;text-shadow:0 1px 2px rgba(0,0,0,.25)}
.dots{left:776px;top:385px;display:flex;gap:7px}
.dots span{width:11px;height:11px;border-radius:50%;background:#b9cde8}
.dots span.on{background:var(--plum);border:2px solid #fff}
.band{left:0;top:454px;width:1034px;height:58px;background:linear-gradient(#fff,#f1f1f1);border-top:3px solid var(--plum)}
.services{left:0;top:0}
.svc{position:absolute;width:140px;margin-left:-70px;text-align:center;top:424px}
.svc .disc{width:52px;height:52px;margin:0 auto;border-radius:50%;background:var(--icon);border:3px solid #fff;box-shadow:0 2px 4px rgba(0,0,0,.35);display:flex;align-items:center;justify-content:center}
.svc.active .disc{background:var(--plum);border-bottom-color:var(--gold)}
.svc p{margin-top:11px;font-family:"Ubuntu",sans-serif;font-weight:500;font-size:10.5px;color:#333}
.h2{font-family:"Ubuntu",sans-serif;font-style:italic;font-weight:700;font-size:17px;color:var(--plum);text-transform:uppercase;letter-spacing:-.3px}
.section-head{border-bottom:1px solid var(--line);padding:0 0 4px 1px}
.about{left:198px;top:532px;width:414px}
.about p{font-size:10.4px;line-height:18.2px;margin-top:12px;color:#333}
.about p+p{margin-top:13px}
.readmore{display:block;text-align:right;margin-top:6px;font-size:10.5px;color:var(--gold);font-family:"Ubuntu",sans-serif}
.team{left:642px;top:528px;width:192px;height:192px;border-radius:50%;border:3px solid var(--plum);overflow:hidden;background:#fff;box-shadow:0 6px 8px rgba(0,0,0,.15)}
.team .photo{position:absolute;left:0;top:0;width:100%;height:100%;background:linear-gradient(#f3f5f8,#c9d4e2)}
.team .label{position:absolute;left:0;top:130px;width:100%;height:70px;background:var(--plum);color:#fff;text-align:center;font-family:"Ubuntu",sans-serif;font-weight:500;font-size:20px;padding-top:10px}
.col{top:756px;width:310px}
.card{margin-top:11px;height:225px;background:var(--panel);border:1px solid #d4d4d4;border-radius:3px;box-shadow:inset 0 0 0 4px #fff,0 6px 6px -3px rgba(0,0,0,.2);padding:4px}
.pager{display:flex;justify-content:center;gap:8px;margin-top:5px}
.testi{display:flex;padding:10px 6px 0 8px;height:110px}
.testi+.testi{border-top:1px solid #dcdcdc}
.person{width:86px;text-align:center}
.avatar{width:60px;height:60px;margin:0 auto;border-radius:50%;border:3px solid #fff;background:linear-gradient(#c7ccd3,#7d8790);box-shadow:0 1px 3px rgba(0,0,0,.3)}
.person b{display:block;font-family:"Ubuntu",sans-serif;font-weight:500;font-size:12px;margin-top:4px}
.person i{font-style:normal;font-size:8.5px;color:#777}
.quote{position:relative;flex:1;border-left:1px solid #e0e0e0;margin-left:12px;padding:15px 0 0 20px;font-size:9px;line-height:13.5px;color:#444}
.quote::before{content:"\201C";position:absolute;left:8px;top:0;font-family:Georgia,serif;font-size:22px;color:#888}
.quote .close{font-family:Georgia,serif;font-size:18px;color:#888;vertical-align:-6px}
.news-item{display:flex;gap:16px;padding:14px 20px 0 20px;height:75px}
.news-item+.news-item{border-top:1px solid #e2e2e2;margin:0 20px;padding:14px 0 0 0}
.news-item time{display:block;font-family:"Ubuntu",sans-serif;font-weight:500;font-size:9.5px;color:var(--plum)}
.news-item p{font-family:"Ubuntu",sans-serif;font-size:9.8px;line-height:13.6px;color:#333;margin-top:6px}
.footer{left:0;top:1058px;width:1034px;height:120px;background:var(--footer);color:#fff}
.footer h3{font-family:"Ubuntu",sans-serif;font-weight:400;font-size:13px;position:absolute;top:12px}
.links{position:absolute;top:46px;left:198px;display:grid;grid-template-columns:85px 85px;row-gap:7px;font-family:"Ubuntu",sans-serif;font-size:8.5px;text-transform:uppercase;list-style:none}
.links li::before{content:"›";color:var(--gold);margin-right:8px}
.divider{position:absolute;top:45px;height:56px;border-left:1px solid #4a4a4a}
.news-form{position:absolute;left:430px;top:40px;width:150px;font-size:9px;line-height:10.5px}
.news-form .field{margin-top:6px;width:114px;height:17px;background:#fff;border-radius:2px;color:#999;font-size:8px;padding:3px 6px}
.news-form .btn{margin-top:7px;width:53px;height:17px;background:var(--plum);border:1px solid #fff;border-radius:2px;text-align:center;font-family:"Ubuntu",sans-serif;font-weight:700;font-size:9px;line-height:15px}
.map{position:absolute;left:635px;top:42px;width:81px;height:62px;background:linear-gradient(135deg,#e7e5df,#cfd6cf)}
.contact{position:absolute;left:728px;top:44px;width:120px;font-size:8.8px;line-height:10.5px;list-style:none}
.contact li{position:relative;padding-left:19px;margin-bottom:5px}
.contact svg{position:absolute;left:0;top:0}
.copy{left:0;top:1178px;width:1034px;height:22px;background:var(--plum);color:#fff;text-align:center;font-family:"Ubuntu",sans-serif;font-size:10px;line-height:22px}
</style>
</head>
<body>
<div class="abs topbar"></div>

<header>
  <div class="abs brand"><span class="brand-mark"></span><span class="brand-name">plumbwick</span></div>
  <div class="abs callus">CALL US: 020 7946 0321</div>
  <div class="abs social" aria-label="Social links"><span></span><span></span><span></span><span></span></div>
  <nav class="abs nav">
    <a class="active">Home</a><a>About Us</a><a>What We Do</a><a>News Blog</a><a>Articles</a><a>Clients</a><a>Partners</a><a>Contact Us</a>
  </nav>
</header>

<section>
  <div class="abs hero" role="img" aria-label="Man touching a transparent screen against a blue sky with clouds"></div>
  <div class="abs hero-photo"></div>
  <div class="abs hero-title">Serious IT support for business</div>
  <div class="abs dots"><span class="on"></span><span></span><span></span><span></span></div>
  <div class="abs band"></div>
  <div class="abs services">
    <div class="svc" style="left:258px"><div class="disc"><svg width="26" height="26" viewBox="0 0 26 26"><path d="M4 22 L14 12" stroke="#fff" stroke-width="4" stroke-linecap="round"/><circle cx="17" cy="9" r="5" fill="none" stroke="#fff" stroke-width="3"/></svg></div><p>It Support &amp; Management</p></div>
    <div class="svc" style="left:390px"><div class="disc"><svg width="30" height="22" viewBox="0 0 30 22"><path d="M8 19 H23 A5 5 0 0 0 23 9 A7 7 0 0 0 10 7 A6 6 0 0 0 8 19 Z" fill="none" stroke="#fff" stroke-width="2.4"/></svg></div><p>Cloud Computing</p></div>
    <div class="svc active" style="left:520px"><div class="disc"><svg width="22" height="28" viewBox="0 0 22 28"><path d="M11 2 C15 7 17 9 17 13 A6 6 0 0 1 5 13 C5 9 8 7 11 2 Z" fill="#fff"/><rect x="7" y="17" width="8" height="9" rx="1" fill="#fff"/></svg></div><p>Disaster Recovery</p></div>
    <div class="svc" style="left:651px"><div class="disc"><svg width="20" height="28" viewBox="0 0 20 28"><rect x="5" y="2" width="10" height="17" rx="1.5" fill="#fff"/><path d="M10 19 V24 M3 25 H17" stroke="#fff" stroke-width="2"/></svg></div><p>Virtualisation</p></div>
    <div class="svc" style="left:774px"><div class="disc"><svg width="28" height="26" viewBox="0 0 28 26"><path d="M14 3 L25 23 H3 Z" fill="none" stroke="#fff" stroke-width="3" stroke-linejoin="round"/><path d="M8 16 H20" stroke="#fff" stroke-width="2.5"/></svg></div><p>CAD Services</p></div>
  </div>
</section>

<main>
  <section class="abs about">
    <h2 class="h2 section-head">About Us</h2>
    <p>Lorem ipsum dolor sit amet, consectetuer adipiscing elit, sed diam nonummy nibh euismod tincidunt ut laoreet dolore magna aliquam erat volutpat. Ut wisi enim ad minim venia m, quis nostrud exerci tation ullamcorper suscipit lobortis nisl ut aliquip ex ea comsed diam nonummy nibh euism od tincidunt ut laoreet dolore magna aliquam erat volutpat.</p>
    <p>Lorem ipsum dolor sit amet, consectetuer adipiscing elit, sed diam nonummy nibh euismod tincidunt ut laoreet dolore magna aliquam erat volutpat. Ut wisi enim ad minim venia m, quis nostrud....</p>
    <a class="readmore">READ MORE...</a>
  </section>

  <div class="abs team">
    <div class="photo" role="img" aria-label="Group photo of the company team"></div>
    <div class="label">OUR TEAM</div>
  </div>

  <section class="abs col" style="left:198px">
    <h2 class="h2 section-head">Testimonials</h2>
    <div class="card">
      <div class="testi">
        <div class="person"><div class="avatar" role="img" aria-label="Portrait of client"></div><b>Dale Fenwick</b><i>Businessman</i></div>
        <p class="quote">Lorem ipsum dolor sit amet, consectetuer adipiscing elit, sed diam nonummyol nibh euismod tincidunt ut laoreet dolore magnarpl aliquam erat volutpat. Ut wisi enim adm minim. <span class="close">&#8221;</span></p>
      </div>
      <div class="testi">
        <div class="person"><div class="avatar" role="img" aria-label="Portrait of client"></div><b>Dale Fenwick</b><i>Businessman</i></div>
        <p class="quote">Lorem ipsum dolor sit amet, consectetuer adipiscing elit, sed diam nonummyol nibh euismod tincidunt ut laoreet dolore magnarpl aliquam erat volutpat. Ut wisi enim adm minim.<span class="close">&#8221;</span></p>
      </div>
    </div>
    <div class="pager">
      <svg width="14" height="14" viewBox="0 0 14 14"><circle cx="7" cy="7" r="6" fill="none" stroke="#555"/><path d="M10 7 H4 M6.5 4.5 L4 7 L6.5 9.5" fill="none" stroke="#555"/></svg>
      <svg width="14" height="14" viewBox="0 0 14 14"><circle cx="7" cy="7" r="6" fill="none" stroke="#555"/><path d="M4 7 H10 M7.5 4.5 L10 7 L7.5 9.5" fill="none" stroke="#555"/></svg>
    </div>
  </section>

  <section class="abs col" style="left:534px">
    <h2 class="h2 section-head">Latest News</h2>
    <div class="card">
      <div class="news-item">
        <svg width="30" height="30" viewBox="0 0 30 30"><rect x="2" y="5" width="26" height="23" rx="3" fill="none" stroke="#555" stroke-width="2"/><path d="M8 2 V8 M22 2 V8 M2 11 H28" stroke="#555" stroke-width="2"/><g fill="#555"><rect x="7" y="14" width="4" height="4"/><rect x="13" y="14" width="4" height="4"/><rect x="19" y="14" width="4" height="4"/><rect x="7" y="20" width="4" height="4"/><rect x="13" y="20" width="4" height="4"/><rect x="19" y="20" width="4" height="4"/></g></svg>
        <div><time>12-APR-2014</time><p>Lorem ipsum dolor sit amet, consectetuer adipiscil ng elit, sed diam nonummy nibh...</p></div>
      </div>
      <div class="news-item">
        <svg width="30" height="30" viewBox="0 0 30 30"><rect x="2" y="5" width="26" height="23" rx="3" fill="none" stroke="#555" stroke-width="2"/><path d="M8 2 V8 M22 2 V8 M2 11 H28" stroke="#555" stroke-width="2"/><g fill="#555"><rect x="7" y="14" width="4" height="4"/><rect x="13" y="14" width="4" height="4"/><rect x="19" y="14" width="4" height="4"/><rect x="7" y="20" width="4" height="4"/><rect x="13" y="20" width="4" height="4"/><rect x="19" y="20" width="4" height="4"/></g></svg>
        <div><time>15-APR-2014</time><p>Lorem ipsum dolor sit amet, consectetuer adipiscil ng elit, sed diam nonummy nibh...</p></div>
      </div>
      <div class="news-item">
        <svg width="30" height="30" viewBox="0 0 30 30"><rect x="2" y="5" width="26" height="23" rx="3" fill="none" stroke="#555" stroke-width="2"/><path d="M8 2 V8 M22 2 V8 M2 11 H28" stroke="#555" stroke-width="2"/><g fill="#555"><rect x="7" y="14" width="4" height="4"/><rect x="13" y="14" width="4" height="4"/><rect x="19" y="14" width="4" height="4"/><rect x="7" y="20" width="4" height="4"/><rect x="13" y="20" width="4" height="4"/><rect x="19" y="20" width="4" height="4"/></g></svg>
        <div><time>17-APR-2014</time><p>Lorem ipsum dolor sit amet, consectetuer adipiscil ng elit, sed diam nonummy nibh...</p></div>
      </div>
    </div>
    <div class="pager">
      <svg width="14" height="14" viewBox="0 0 14 14"><circle cx="7" cy="7" r="6" fill="none" stroke="#555"/><path d="M10 7 H4 M6.5 4.5 L4 7 L6.5 9.5" fill="none" stroke="#555"/></svg>
      <svg width="14" height="14" viewBox="0 0 14 14"><circle cx="7" cy="7" r="6" fill="none" stroke="#555"/><path d="M4 7 H10 M7.5 4.5 L10 7 L7.5 9.5" fill="none" stroke="#555"/></svg>
    </div>
  </section>
</main>

<footer class="abs footer">
  <h3 style="left:198px">Quick Links</h3>
  <ul class="links">
    <li>Home</li><li>Articles</li><li>About Us</li><li>Clients</li><li>What We Do</li><li>Partners</li><li>News Blog</li><li>Contact Us</li>
  </ul>
  <div class="divider" style="left:388px"></div>
  <h3 style="left:430px">Newsletter Signup</h3>
  <div class="news-form">
    <p>Lorem ipsum dolor sit amet, consectetuer adipiscing elit.</p>
    <div class="field">Enter your email address</div>
    <div class="btn">SUBMIT</div>
  </div>
  <div class="divider" style="left:593px"></div>
  <h3 style="left:635px">Contact Info</h3>
  <div class="map" role="img" aria-label="Street map showing the office location"></div>
  <ul class="contact">
    <li><svg width="10" height="12" viewBox="0 0 10 12"><path d="M5 11 C2 7 1 5.5 1 4 A4 4 0 0 1 9 4 C9 5.5 8 7 5 11 Z" fill="var(--gold)"/><circle cx="5" cy="4" r="1.5" fill="#333"/></svg>Lorem ipsum dolor sit amet, consectetuer adipiscing elit.</li>
    <li><svg width="11" height="11" viewBox="0 0 11 11"><circle cx="5.5" cy="5.5" r="5" fill="none" stroke="var(--gold)"/><path d="M3.5 3 L4.5 3 L5 4.5 L4.3 5 Q5 6.5 6 6.8 L6.5 6 L8 6.5 L8 7.5 Q5 8.5 3.5 3 Z" fill="var(--gold)"/></svg>020 7946 0321</li>
    <li><svg width="11" height="9" viewBox="0 0 11 9"><rect x=".5" y=".5" width="10" height="8" fill="var(--gold)"/><path d="M.5 .5 L5.5 5 L10.5 .5" fill="none" stroke="#333"/></svg>website@plumbwick.net</li>
  </ul>
</footer>
<div class="abs copy">© 2014 plumbwick. All Rights Reserved.</div>
</body>
</html>
```